Business Card for a Dental Office

The design should communicate integrity, quality and reliability. We also want the card look elegant, simple, but still stand out, different from the traditional-dental-office business card.

Industry/Entity Type

Business

```html
<!DOCTYPE html>
<html lang="en">
<head>
<meta charset="utf-8">
<title>Halden Dental Studio – Business Card</title>
<link rel="stylesheet" href="https://fonts.googleapis.com/css2?family=Oswald:wght@500;600&family=Arimo:wght@400;700&display=swap">
<style>
  :root {
    --bg: #3a3b3d;
    --gold-light: #f2e433;
    --gold: #d9c21a;
    --gold-deep: #a8900c;
    --ink: #111111;
    --white: #ffffff;
    --card-black: #0b0b0b;
  }
  * { box-sizing: border-box; margin: 0; padding: 0; }
  html, body { width: 1200px; height: 950px; overflow: hidden; }
  body {
    background: var(--bg);
    font-family: "Arimo", Arial, sans-serif;
    position: relative;
  }
  .card {
    position: absolute;
    left: 250px;
    width: 700px;
    height: 400px;
    overflow: hidden;
    box-shadow: 0 10px 28px rgba(0,0,0,.45);
  }

  /* Front */
  .card-front {
    top: 40px;
    background: radial-gradient(ellipse at 55% 40%, var(--gold-light) 0%, var(--gold) 45%, var(--gold-deep) 100%);
  }
  .front-brand {
    position: absolute;
    top: 150px;
    left: 0; right: 0;
    display: flex;
    justify-content: center;
    align-items: center;
    gap: 14px;
  }
  .brand-mark {
    width: 34px; height: 34px;
    background: var(--ink);
  }
  .brand-name {
    font-family: "Oswald", "Arial Narrow", sans-serif;
    font-weight: 600;
    font-size: 38px;
    letter-spacing: .5px;
    color: var(--ink);
    text-transform: uppercase;
    white-space: nowrap;
  }
  .front-web {
    position: absolute;
    top: 262px; left: 0; right: 0;
    text-align: center;
    font-size: 17px;
    letter-spacing: 3px;
    color: var(--ink);
  }

  /* Back */
  .card-back { top: 500px; background: var(--card-black); }
  .card-back svg.back-shape { position: absolute; inset: 0; }
  .back-brand {
    position: absolute;
    top: 150px; left: 40px;
    display: flex; align-items: center; gap: 10px;
  }
  .back-brand .brand-mark { width: 26px; height: 26px; }
  .back-brand .brand-name { font-size: 26px; }
  .person {
    position: absolute;
    top: 226px; left: 40px;
    width: 300px;
    text-align: center;
  }
  .person-name {
    font-family: "Oswald", "Arial Narrow", sans-serif;
    font-weight: 500;
    font-size: 21px;
    color: var(--ink);
    letter-spacing: .5px;
  }
  .person-role {
    font-family: "Oswald", "Arial Narrow", sans-serif;
    font-weight: 500;
    font-size: 14px;
    color: var(--gold);
    letter-spacing: 1px;
  }
  .contact-list {
    position: absolute;
    top: 68px; right: 28px;
    list-style: none;
    text-align: right;
  }
  .contact-list li {
    display: flex; justify-content: flex-end; align-items: center;
    gap: 10px;
    font-size: 16px;
    color: var(--white);
    height: 29px;
    white-space: nowrap;
  }
  .contact-list svg { width: 18px; height: 18px; flex: none; }
  .address {
    position: absolute;
    right: 28px; bottom: 36px;
    font-size: 17px;
    color: var(--white);
    white-space: nowrap;
  }
</style>
</head>
<body>

<section class="card card-front" aria-label="Card front">
  <div class="front-brand">
    <span class="brand-mark"></span>
    <span class="brand-name">Halden Dental Studio</span>
  </div>
  <p class="front-web">www.haldendental.com</p>
</section>

<section class="card card-back" aria-label="Card back">
  <svg class="back-shape" width="700" height="400" viewBox="0 0 700 400">
    <defs>
      <linearGradient id="goldStroke" x1="0" y1="0" x2="0" y2="1">
        <stop offset="0" stop-color="#f2e433"/>
        <stop offset=".5" stop-color="#d9c21a"/>
        <stop offset="1" stop-color="#f2e433"/>
      </linearGradient>
    </defs>
    <path d="M0 0 H400 Q470 200 200 400 H0 Z" fill="var(--white)"/>
    <path d="M396 -2 Q492 200 196 402 Q470 200 396 -2 Z" fill="url(#goldStroke)"/>
  </svg>

  <div class="back-brand">
    <span class="brand-mark"></span>
    <span class="brand-name">Halden Dental Studio</span>
  </div>

  <div class="person">
    <p class="person-name">MARA QUILL</p>
    <p class="person-role">PRESIDENT</p>
  </div>

  <ul class="contact-list">
    <li>512 6039 4471
      <svg viewBox="0 0 20 20"><path d="M5 2l3 4-2 2c1 3 3 5 6 6l2-2 4 3-2 3C8 18 2 12 2 4z" fill="var(--gold)"/></svg></li>
    <li>734 2816 9052
      <svg viewBox="0 0 20 20"><rect x="5" y="1" width="10" height="18" rx="2" fill="var(--gold)"/><rect x="7" y="4" width="6" height="10" fill="var(--card-black)"/></svg></li>
    <li>629 5180 7734
      <svg viewBox="0 0 20 20"><rect x="2" y="7" width="16" height="9" rx="1" fill="var(--gold)"/><rect x="5" y="2" width="10" height="6" fill="var(--gold)"/><rect x="5" y="12" width="10" height="6" fill="var(--white)"/></svg></li>
    <li>mara@haldendental.com
      <svg viewBox="0 0 20 20"><rect x="1" y="4" width="18" height="12" fill="var(--gold)"/><path d="M1 4l9 7 9-7" fill="none" stroke="var(--card-black)" stroke-width="1.5"/></svg></li>
    <li>www.haldendental.com
      <svg viewBox="0 0 20 20"><circle cx="10" cy="10" r="8" fill="var(--gold)"/><path d="M2 10h16M10 2c-4 5-4 11 0 16M10 2c4 5 4 11 0 16" fill="none" stroke="var(--card-black)" stroke-width="1.2"/></svg></li>
  </ul>

  <p class="address">4127 Alder Crest Road, Linwood, NY 10492</p>
</section>

</body>
</html>
```